Revamp Marketing Website For Video Production Website

need to revamp current website www.kestrelfilmstudio.net
reference sites www.vantora.net & http://layoutcrate.net/kestrel/
Use all current content on current kestrel website. I want a revamped modenr look. Sometbing that wows customers.
reference site www.vantora.net
Target Market(s)
business owners
Industry/Entity Type
Video Production
Number of Pages Required
5+ page
Colors
Designer to choose colors to be used in the design.
Requirements
Must have
- need to revamp current website www.kestrelfilmstudio.net
- reference sites www.vantora.net & http://layoutcrate.net/kestrel/
- Use all current content on current kestrel website. I want a revamped modenr look. Sometbing that wows customers.
- reference site www.vantora.net
Nice to have
Should not have

```html
<!DOCTYPE html>
<html lang="en">
<head>
<meta charset="utf-8">
<title>Kestrel – Marketing Videos Made For You</title>
<link href="https://fonts.googleapis.com/css2?family=Montserrat:wght@400;500;700;800&family=Oswald:wght@300;400;500&display=swap" rel="stylesheet">
<style>
:root{
  --blue:#0a8fe8;
  --blue-deep:#0a6ff0;
  --blue-light:#18b4ec;
  --ink:#111;
  --text:#555;
  --muted:#888;
  --white:#fff;
  --line:#e3e6ea;
}
*{margin:0;padding:0;box-sizing:border-box}
html,body{width:1200px;height:4682px;overflow:hidden;background:var(--white)}
body{position:relative;font-family:'Montserrat',sans-serif;color:var(--text)}
h1,h2,h3,h4{font-weight:400}
.abs{position:absolute}
.accent{color:var(--blue)}

/* header */
.brand{position:absolute;left:78px;top:20px}
.brand-name{font-family:'Montserrat',sans-serif;font-weight:800;font-size:38px;letter-spacing:3px;color:#1b1f2a;line-height:1}
.brand-tag{font-size:11.5px;font-weight:700;color:#1b1f2a;letter-spacing:.3px;margin-top:6px}
.nav{position:absolute;top:34px;left:412px;display:flex;gap:31px;font-size:14px;color:#333;font-weight:500}
.nav .active{color:var(--blue)}
.btn-signup{position:absolute;left:1034px;top:25px;width:88px;height:39px;border-radius:4px;background:var(--blue);color:#fff;font-size:14px;font-weight:600;display:flex;align-items:center;justify-content:center}

/* hero */
.hero-title{position:absolute;left:78px;top:246px;font-size:66px;font-weight:800;color:var(--ink);letter-spacing:-1px;line-height:1.15}
.hero-sub{position:absolute;left:80px;top:334px;font-size:24px;font-weight:700;color:#222;line-height:1.2}
.hero-bar{position:absolute;left:80px;top:357px;width:377px;height:11px;background:var(--blue-light)}
.hero-note{position:absolute;left:82px;top:386px;font-size:14px;color:#333}
.social{position:absolute;display:flex;gap:3px}
.social span{width:47px;height:47px;border-radius:50%;display:block}
.s1{background:#3b5a9a}.s2{background:#d8255f}.s3{background:#dc4a38}.s4{background:#e0261c}.s5{background:#1aa9d3}.s6{background:#1072b0}.s7{background:#cb1f27}.s8{background:#1da1f2}
.collage-frame{position:absolute;background:#fff;box-shadow:0 8px 24px rgba(0,0,0,.15);border-radius:6px;padding:10px}
.collage-frame div{width:100%;height:100%}
.dot{position:absolute;border-radius:50%}

/* promote band */
.band-promote{position:absolute;left:0;top:676px;width:1200px;height:315px;background:linear-gradient(90deg,var(--blue-deep),var(--blue-light));text-align:center;color:#fff}
.band-promote h2{font-family:'Oswald',sans-serif;font-weight:400;font-size:58px;margin-top:54px;line-height:1.1}
.band-promote h3{font-family:'Oswald',sans-serif;font-weight:400;font-size:20px;margin-top:8px}
.band-promote p{font-size:13px;line-height:27px;width:700px;margin:22px auto 0}
.scroll-btn{position:absolute;left:567px;top:952px;width:66px;height:66px;border-radius:50%;background:#fff;display:flex;align-items:center;justify-content:center}
.scroll-btn span{width:50px;height:50px;border-radius:50%;background:var(--blue);display:flex;align-items:center;justify-content:center}

/* section titles */
.sec-title{position:absolute;font-family:'Oswald',sans-serif;font-weight:400;font-size:50px;color:var(--ink);line-height:1}

/* examples */
.select{position:absolute;left:913px;top:1082px;width:209px;height:54px;border:1px solid var(--line);border-radius:27px;font-size:13px;color:#777;padding:18px 0 0 24px}
.select svg{position:absolute;right:18px;top:22px}
.example{position:absolute;top:1182px;width:276px;height:332px;overflow:hidden}
.example .ph{width:100%;height:100%}
.example .label{position:absolute;left:19px;bottom:20px;font-family:'Oswald',sans-serif;font-size:20px;color:#fff;white-space:nowrap}
.example .play{position:absolute;right:14px;bottom:14px;width:42px;height:42px;border-radius:50%;background:var(--blue);display:flex;align-items:center;justify-content:center}

/* features */
.features{position:absolute;left:0;top:1570px;width:1200px;height:615px}
.feat{position:absolute;width:200px;text-align:center}
.feat .ico{width:84px;height:84px;margin:0 auto;background:#fff;border-radius:8px;box-shadow:0 6px 14px rgba(0,0,0,.15);display:flex;align-items:center;justify-content:center}
.feat .ico svg{width:48px;height:48px}
.feat p{font-family:'Oswald',sans-serif;font-size:15px;color:#fff;margin-top:24px}

/* video sizes */
.lead{position:absolute;left:330px;width:540px;text-align:center;font-size:13px;line-height:27px;color:var(--text)}
.size-ico{position:absolute;width:87px;height:87px;border-radius:50%;background:#fff;box-shadow:0 4px 14px rgba(0,0,0,.12);display:flex;align-items:center;justify-content:center}
.size-title{position:absolute;font-family:'Oswald',sans-serif;font-weight:400;font-size:46px;color:var(--ink);line-height:1;white-space:nowrap}
.size-text{position:absolute;width:400px;font-size:13px;line-height:27px;color:var(--text)}
.btn-more{position:absolute;width:126px;height:47px;border-radius:3px;background:var(--blue);color:#fff;font-family:'Oswald',sans-serif;font-size:16px;display:flex;align-items:center;justify-content:center}
.photo{position:absolute;background:#fff;box-shadow:0 6px 18px rgba(0,0,0,.18);padding:8px}
.photo div{width:100%;height:100%}

/* cta */
.cta{position:absolute;left:425px;top:4045px;width:350px;height:76px;border-radius:4px;background:var(--blue);color:#fff;text-align:center}
.cta b{display:block;font-family:'Oswald',sans-serif;font-weight:400;font-size:20px;margin-top:14px}
.cta small{font-size:12px}

/* bottom band */
.band-award{position:absolute;left:0;top:4187px;width:1200px;height:189px;background:linear-gradient(90deg,var(--blue-deep),var(--blue-light))}
.band-award h4{position:absolute;left:78px;top:46px;font-family:'Oswald',sans-serif;font-weight:400;font-size:29px;line-height:42px;color:#fff}

/* footer */
.footer{position:absolute;left:0;top:4420px;width:1200px;text-align:center}
.footer .brand-name{font-size:34px}
.footer-links{font-size:13px;color:#666;margin-top:30px}
.footer-links i{font-style:normal;margin:0 10px;color:#aaa}
.footer-mail{font-size:13px;color:#444;margin-top:30px}
.footer-copy{font-size:13px;color:#555;margin-top:12px}
</style>
</head>
<body>

<header>
  <div class="brand">
    <div class="brand-name">KESTREL</div>
    <div class="brand-tag">MARKETING VIDEOS MADE FOR YOU</div>
  </div>
  <nav class="nav">
    <span class="active">Home</span><span>How It Works</span><span>Examples</span><span>Faq</span><span>Contact Us</span><span>Pricing</span><span>Login</span>
  </nav>
  <div class="btn-signup">Sign Up</div>
</header>

<section class="hero">
  <h1 class="hero-title">ATTENTION</h1>
  <div class="hero-bar"></div>
  <div class="hero-sub" style="z-index:1">GRABBING VIDEO ADS</div>
  <div class="hero-note">DELIVERED IN 24 HOURS!</div>
  <div class="social" style="left:77px;top:436px">
    <span class="s1"></span><span class="s2"></span><span class="s3"></span><span class="s4"></span><span class="s5"></span><span class="s6"></span><span class="s7"></span><span class="s8"></span>
  </div>

  <div class="collage-frame" style="left:800px;top:150px;width:420px;height:300px;transform:rotate(12deg);opacity:.5"><div style="background:#eef1f4"></div></div>
  <div class="collage-frame" style="left:530px;top:400px;width:185px;height:210px;transform:rotate(10deg)"><div role="img" aria-label="Photo of a DJ at a mixing deck" style="background:linear-gradient(160deg,#b9c6d2,#3c4a5a)"></div></div>
  <div class="collage-frame" style="left:700px;top:320px;width:250px;height:270px;transform:rotate(10deg)"><div role="img" aria-label="Photo of a man outdoors against a blue sky" style="background:linear-gradient(170deg,#6fa7d8,#b07a4e)"></div></div>
  <div class="collage-frame" style="left:690px;top:255px;width:90px;height:70px;transform:rotate(10deg)"><div role="img" aria-label="Photo of a woman with red hair" style="background:linear-gradient(160deg,#e05b3d,#6a1d1d)"></div></div>
  <div class="collage-frame" style="left:1040px;top:250px;width:160px;height:180px;transform:rotate(12deg)"><div role="img" aria-label="Photo of a woman on a yellow background" style="background:linear-gradient(160deg,#f7d21b,#2a9fd8)"></div></div>
  <div class="collage-frame" style="left:945px;top:460px;width:90px;height:80px;transform:rotate(12deg)"><div role="img" aria-label="Photo of a smiling woman in orange" style="background:linear-gradient(160deg,#f08a2b,#2d6f57)"></div></div>
  <div class="collage-frame" style="left:1020px;top:540px;width:180px;height:150px;transform:rotate(12deg)"><div role="img" aria-label="Photo of a pineapple on turquoise" style="background:linear-gradient(160deg,#2cc3d9,#e4b23a)"></div></div>
  <div class="dot" style="left:657px;top:310px;width:46px;height:46px;background:#f6c43a"></div>
  <div class="dot" style="left:1002px;top:370px;width:50px;height:50px;background:#5b63e6"></div>
  <div class="dot" style="left:793px;top:585px;width:48px;height:48px;background:#ee3d5a;display:flex;align-items:center;justify-content:center">
    <svg width="22" height="20" viewBox="0 0 24 22"><path d="M12 21 2.5 11.5a5.5 5.5 0 0 1 7.8-7.8L12 5.4l1.7-1.7a5.5 5.5 0 0 1 7.8 7.8Z" fill="#fff"/></svg>
  </div>
</section>

<section class="band-promote">
  <h2>Promote Anything</h2>
  <h3>ANYWHERE ON THE WEB</h3>
  <p>Still using static image ads with Pagewall, Photoreel, Workline, Blinkchat advertising platforms? Turn them into VIDEO ADS and get higher conversion rates instantly.</p>
</section>
<div class="scroll-btn"><span><svg width="20" height="12" viewBox="0 0 20 12"><path d="M2 2l8 8 8-8" stroke="#fff" stroke-width="2.5" fill="none"/></svg></span></div>

<section class="examples">
  <h2 class="sec-title" style="left:77px;top:1084px">Our <span class="accent">Examples</span></h2>
  <div class="select">Summer <svg width="16" height="10" viewBox="0 0 16 10"><path d="M0 0h16L8 10z" fill="var(--blue)"/></svg></div>
  <div class="example" style="left:189px"><div class="ph" role="img" aria-label="Woman in swimwear walking on a beach" style="background:linear-gradient(180deg,#dfe5ea,#8e9ba6)"></div><div class="label">Summer Demo 1</div><div class="play"><svg width="14" height="16" viewBox="0 0 14 16"><path d="M0 0l14 8-14 8z" fill="#fff"/></svg></div></div>
  <div class="example" style="left:485px"><div class="ph" role="img" aria-label="Orange ice lolly on a light surface" style="background:linear-gradient(180deg,#f1eee7,#d7a24a)"></div><div class="label">Summer Demo 1</div><div class="play"><svg width="14" height="16" viewBox="0 0 14 16"><path d="M0 0l14 8-14 8z" fill="#fff"/></svg></div></div>
  <div class="example" style="left:782px"><div class="ph" role="img" aria-label="Surfer paddling near mountains" style="background:linear-gradient(180deg,#9cc2dc,#2e6d78)"></div><div class="label">Summer Demo 1</div><div class="play"><svg width="14" height="16" viewBox="0 0 14 16"><path d="M0 0l14 8-14 8z" fill="#fff"/></svg></div></div>
  <div class="example" style="left:1078px"><div class="ph" role="img" aria-label="Summer scene preview" style="background:linear-gradient(180deg,#c3ccd3,#8a96a0)"></div><div class="label">Summer Demo 1</div></div>
</section>

<svg class="abs" style="left:0;top:1570px" width="1200" height="615" viewBox="0 0 1200 615">
  <defs><linearGradient id="fg" x1="0" x2="1"><stop offset="0" stop-color="#0a6ff0"/><stop offset="1" stop-color="#18b4ec"/></linearGradient></defs>
  <path d="M0 85C220 0 420 85 620 85S1000 40 1200 0V615H0Z" fill="url(#fg)"/>
</svg>
<section class="features">
  <h2 class="sec-title" style="left:0;width:1200px;text-align:center;top:142px;color:#111">Our <span style="color:#fff">Feature</span></h2>
  <div class="feat" style="left:75px;top:243px"><div class="ico"><svg viewBox="0 0 48 48"><rect x="5" y="9" width="34" height="34" rx="5" fill="none" stroke="var(--blue)" stroke-width="4"/><path d="M14 25l7 7L43 8" stroke="var(--blue)" stroke-width="4.5" fill="none"/></svg></div><p>DONE FOR YOU</p></div>
  <div class="feat" style="left:285px;top:243px"><div class="ico"><svg viewBox="0 0 48 48"><path d="M14 36h-2a9 9 0 0 1-1-18 12 12 0 0 1 23-3 10 10 0 0 1 2 21h-2Z" fill="var(--blue)"/><path d="M24 38V24m-6 5 6-6 6 6" stroke="#fff" stroke-width="3.5" fill="none"/></svg></div><p>PREMIUM CONTENT</p></div>
  <div class="feat" style="left:500px;top:243px"><div class="ico"><svg viewBox="0 0 48 48"><rect x="2" y="13" width="44" height="22" rx="3" fill="var(--blue)"/><path d="M11 17l2 4 4 .5-3 3 1 4-4-2-4 2 1-4-3-3 4-.5zM24 17l2 4 4 .5-3 3 1 4-4-2-4 2 1-4-3-3 4-.5zM37 17l2 4 4 .5-3 3 1 4-4-2-4 2 1-4-3-3 4-.5z" fill="#fff"/></svg></div><p>FULLY LICENSED TO YOU</p></div>
  <div class="feat" style="left:709px;top:243px"><div class="ico"><svg viewBox="0 0 48 48"><rect x="3" y="12" width="32" height="24" rx="6" fill="var(--blue)"/><path d="M35 20l10-6v20l-10-6z" fill="var(--blue)"/><circle cx="19" cy="24" r="7" fill="#fff"/><circle cx="19" cy="24" r="3.5" fill="var(--blue)"/></svg></div><p>PERFECT LENGTH FOR VIDEO ADS</p></div>
  <div class="feat" style="left:918px;top:243px"><div class="ico"><svg viewBox="0 0 48 48"><rect x="6" y="4" width="36" height="32" rx="2" fill="none" stroke="var(--blue)" stroke-width="3"/><rect x="11" y="10" width="16" height="12" fill="var(--blue)"/><path d="M30 11h8M30 16h8M30 21h8M11 28h27" stroke="var(--blue)" stroke-width="3"/><path d="M20 36v8l6-5" fill="var(--blue)"/></svg></div><p>PAGEWALL VIDEO COVER</p></div>
  <div class="feat" style="left:75px;top:423px"><div class="ico"><svg viewBox="0 0 48 48"><path d="M8 27V22a16 16 0 0 1 32 0v5" stroke="var(--blue)" stroke-width="4" fill="none"/><rect x="4" y="22" width="9" height="15" rx="3" fill="var(--blue)"/><rect x="35" y="22" width="9" height="15" rx="3" fill="var(--blue)"/><path d="M39 37v3a4 4 0 0 1-4 4h-8" stroke="var(--blue)" stroke-width="3" fill="none"/><rect x="21" y="41" width="8" height="5" rx="2" fill="var(--blue)"/></svg></div><p>BEST SUPPORT</p></div>
  <div class="feat" style="left:285px;top:423px"><div class="ico"><svg viewBox="0 0 48 48"><rect x="13" y="3" width="22" height="42" rx="3" fill="var(--blue)"/><rect x="16" y="9" width="16" height="28" fill="#fff"/><path d="M21 18l7 5-7 5z" fill="var(--blue)"/></svg></div><p>VERTICAL VIDEO FORMAT</p></div>
  <div class="feat" style="left:500px;top:423px"><div class="ico"><svg viewBox="0 0 48 48"><rect x="4" y="4" width="40" height="36" rx="3" fill="none" stroke="var(--blue)" stroke-width="3.5"/><rect x="11" y="10" width="26" height="20" fill="var(--blue)"/><path d="M20 14l9 6-9 6z" fill="#fff"/><path d="M4 44h40" stroke="var(--blue)" stroke-width="3.5"/></svg></div><p>SQUARE VIDEO FORMATS</p></div>
  <div class="feat" style="left:709px;top:423px"><div class="ico"><svg viewBox="0 0 48 48"><rect x="4" y="6" width="40" height="36" fill="var(--blue)"/><path d="M8 10h4M16 10h4M24 10h4M32 10h4M8 38h4M16 38h4M24 38h4M32 38h4" stroke="#fff" stroke-width="3"/><path d="M20 18l10 6-10 6z" fill="#fff"/></svg></div><p>FULL H.D. VIDEO FORMATS</p></div>
</section>

<section class="sizes">
  <h2 class="sec-title" style="left:0;width:1200px;text-align:center;top:2255px">Video Size <span class="accent">Available</span></h2>
  <p class="lead" style="top:2318px">With Kestrel, you simply let us know what you want to promote and we will have your video ad finished as soon as 24 hours!</p>

  <div class="abs" role="img" aria-label="Man in a cap holding a drink against a blue door" style="left:77px;top:2455px;width:473px;height:293px;background:linear-gradient(160deg,#45708e,#c99a86 60%,#2f5371)"></div>
  <div class="photo" style="left:40px;top:2387px;width:170px;height:140px"><div role="img" aria-label="People resting on a snowy hillside" style="background:linear-gradient(160deg,#dfe3e6,#6b6f6a)"></div></div>
  <div class="photo" style="left:470px;top:2568px;width:175px;height:140px"><div role="img" aria-label="Glass of lime drink" style="background:linear-gradient(160deg,#3b4a3e,#9fcf5a)"></div></div>
  <div class="photo" style="left:160px;top:2700px;width:165px;height:130px"><div role="img" aria-label="Woman in yellow on turquoise background" style="background:linear-gradient(160deg,#33c7d6,#f2d52c)"></div></div>
  <div class="size-ico" style="left:709px;top:2451px"><svg width="46" height="44" viewBox="0 0 46 44"><rect x="2" y="3" width="42" height="28" rx="2" fill="none" stroke="var(--blue)" stroke-width="2.5"/><path d="M2 24h42M16 40h14M23 31v9" stroke="var(--blue)" stroke-width="2.5"/></svg></div>
  <h3 class="size-title" style="left:722px;top:2553px">Wide Screen <span class="accent">Videos</span></h3>
  <p class="size-text" style="left:725px;top:2612px">This size is a standard video size that works best for pretty much anywhere on the web (1080x720) Included with all video purchases</p>
  <div class="btn-more" style="left:725px;top:2705px">VIEW MORE</div>

  <div class="abs" style="left:660px;top:2925px;width:560px;height:415px;background:#1a1a1a;border-radius:16px 16px 0 0"></div>
  <div class="abs" role="img" aria-label="Smiling woman holding a phone" style="left:677px;top:2945px;width:523px;height:380px;background:linear-gradient(150deg,#3d6b2f,#d8c9b4 55%,#3e5f8b)"></div>
  <div class="abs" style="left:590px;top:3340px;width:610px;height:30px;background:linear-gradient(180deg,#e8e8e8,#a9a9a9);border-radius:0 0 20px 20px"></div>
  <div class="photo" style="left:564px;top:2963px;width:135px;height:140px"><div role="img" aria-label="Man working on a laptop against a wall" style="background:linear-gradient(160deg,#7fb7c8,#b34a3c)"></div></div>
  <div class="photo" style="left:625px;top:3212px;width:135px;height:135px"><div role="img" aria-label="Dancer leaping" style="background:linear-gradient(160deg,#8fa2b8,#7a3f9c)"></div></div>
  <div class="photo" style="left:1103px;top:2900px;width:110px;height:135px"><div role="img" aria-label="Woman on a yellow background" style="background:linear-gradient(160deg,#f1c02b,#b57b1a)"></div></div>
  <div class="size-ico" style="left:76px;top:3009px"><svg width="44" height="44" viewBox="0 0 44 44"><rect x="3" y="3" width="38" height="34" rx="2" fill="none" stroke="var(--blue)" stroke-width="2.5"/><rect x="10" y="9" width="24" height="18" fill="none" stroke="var(--blue)" stroke-width="2.5"/><path d="M19 13l7 5-7 5z" fill="var(--blue)"/><path d="M3 42h38" stroke="var(--blue)" stroke-width="2.5"/></svg></div>
  <h3 class="size-title" style="left:78px;top:3104px">Square <span class="accent">Videos</span></h3>
  <p class="size-text" style="left:78px;top:3168px;width:380px">Square Videos that work best on PAGEWALL (Square is 1080 X 1080) Convert any video to this size for an additional fee of $39</p>
  <div class="btn-more" style="left:76px;top:3263px">VIEW MORE</div>

  <div class="abs" style="left:194px;top:3500px;width:245px;height:482px;border:3px solid #ddd;border-radius:36px;background:#fff"></div>
  <div class="abs" style="left:304px;top:3538px;width:25px;height:3px;background:#222"></div>
  <div class="abs" role="img" aria-label="Masked person sitting on a car under a cloudy sky" style="left:205px;top:3567px;width:223px;height:360px;background:linear-gradient(180deg,#a7b6c4,#4a5360 60%,#2a2f36)"></div>
  <div class="abs" style="left:298px;top:3938px;width:36px;height:36px;border-radius:50%;border:2px solid #444"></div>
  <div class="photo" style="left:87px;top:3552px;width:135px;height:175px"><div role="img" aria-label="Hand holding an ice cream cone" style="background:linear-gradient(160deg,#d7b6a5,#7a5446)"></div></div>
  <div class="photo" style="left:410px;top:3775px;width:135px;height:180px"><div role="img" aria-label="Woman in red among green foliage" style="background:linear-gradient(160deg,#1f5a45,#a42a2a)"></div></div>
  <div class="size-ico" style="left:709px;top:3565px"><svg width="46" height="46" viewBox="0 0 46 46"><rect x="11" y="11" width="24" height="24" rx="3" transform="rotate(45 23 23)" fill="none" stroke="var(--blue)" stroke-width="2.5"/><path d="M5 17a20 20 0 0 1 12-12M41 29a20 20 0 0 1-12 12" stroke="var(--blue)" stroke-width="2.5" fill="none"/></svg></div>
  <h3 class="size-title" style="left:722px;top:3667px">Vertical <span class="accent">Videos</span></h3>
  <p class="size-text" style="left:725px;top:3723px;width:400px">Vertical Videos that work best on STORIES for Pagewall, Photoreel and Blinkchat (1080 X 1920)<br>Convert any video to this size for an additional fee of $39</p>
  <div class="btn-more" style="left:725px;top:3822px">VIEW MORE</div>
</section>

<div class="cta"><b>GET ONE FREE VIDEO MOCKUP NOW</b><small>No Purchase Necessary</small></div>

<section class="band-award">
  <h4>We Create Award Winning Promotional Marketing<br>Videos To Use All Over The Web</h4>
  <div class="social" style="left:724px;top:71px">
    <span class="s1"></span><span class="s2"></span><span class="s3"></span><span class="s4"></span><span class="s5"></span><span class="s6"></span><span class="s7"></span><span class="s8"></span>
  </div>
</section>

<footer class="footer">
  <div class="brand-name">KESTREL</div>
  <div class="brand-tag">MARKETING VIDEOS MADE FOR YOU</div>
  <div class="footer-links">Home<i>|</i>How It Works<i>|</i>Examples<i>|</i>Faq<i>|</i>Contact Us<i>|</i>Pricing</div>
  <div class="footer-mail"><span class="accent">Email Us :</span> support@kestrelfilmstudio.net</div>
  <div class="footer-copy">©KESTREL MARKETING -2019 All Rights Reserved. Term Of Service | Privacy Policy | Cookies Policy</div>
</footer>

</body>
</html>
```